Company letterhead, compliments slip and business card design for Electrical Contracting Company
Colm Tierney Electrical
Corporate
Declan Morrow
Managing DIrector
Clonbeg
Mellick Road
Dundalk
Louth
declan@colmtierney-example.com
www.colmtierney-example.com

```html
<!DOCTYPE html>
<html lang="en">
<head>
<meta charset="utf-8">
<title>Colm Tierney Electrical – Stationery</title>
<link rel="stylesheet" href="https://fonts.googleapis.com/css2?family=Open+Sans:wght@400;600;700&family=Cormorant+Garamond:ital,wght@1,600&display=swap">
<style>
  :root {
    --backdrop: #2e2e30;
    --paper: #ffffff;
    --red: #d3242b;
    --grey-band: #cfcfcf;
    --grey-dark: #8a8a8a;
    --grey-card: #9a9a9a;
    --ink: #333333;
    --ink-soft: #777777;
  }
  * { box-sizing: border-box; margin: 0; padding: 0; }
  html, body { width: 1200px; height: 799px; overflow: hidden; }
  body {
    background: var(--backdrop);
    font-family: "Open Sans", Arial, sans-serif;
    color: var(--ink);
    position: relative;
  }
  .sheet {
    position: absolute;
    background: var(--paper);
    box-shadow: 0 6px 18px rgba(0,0,0,.45);
    overflow: hidden;
  }
  .brand { display: flex; align-items: center; gap: 8px; }
  .brand-square { width: 14px; height: 14px; background: var(--red); flex: none; }
  .brand-name { font-weight: 700; color: var(--red); font-size: 15px; letter-spacing: .3px; white-space: nowrap; }

  .band { position: absolute; left: 0; right: 0; bottom: 0; height: 22px; }
  .band svg { position: absolute; inset: 0; width: 100%; height: 100%; }
  .band-web {
    position: absolute; left: 30%; top: 50%; transform: translateY(-50%);
    font-size: 7px; letter-spacing: 2px; color: #ffffff; white-space: nowrap;
  }

  /* Letterhead */
  .letterhead { left: 40px; top: 50px; width: 495px; height: 700px; }
  .letterhead .brand { position: absolute; left: 38px; top: 44px; }
  .letterhead .contact {
    position: absolute; right: 38px; top: 40px;
    font-size: 7.5px; line-height: 1.75; color: var(--ink-soft);
  }
  .contact-line { display: flex; align-items: center; gap: 6px; white-space: nowrap; }
  .contact-dot { width: 5px; height: 5px; background: var(--red); flex: none; }

  /* Compliments slip */
  .slip { left: 575px; top: 50px; width: 585px; height: 210px; }
  .slip .brand { position: absolute; left: 30px; top: 62px; }
  .slip .brand-name { font-size: 18px; }
  .slip .brand-square { width: 16px; height: 16px; }
  .slip-greeting {
    position: absolute; right: 34px; top: 120px;
    font-family: "Cormorant Garamond", Georgia, serif;
    font-style: italic; font-weight: 600; font-size: 22px; color: var(--ink);
  }

  /* Business cards */
  .card { width: 280px; height: 160px; }
  .card-back { left: 575px; top: 310px; background: var(--grey-card); display: flex; align-items: center; justify-content: center; }
  .card-back .brand-name { color: #ffffff; font-size: 14px; }
  .card-back .brand-square { background: #ffffff; width: 12px; height: 12px; }

  .card-front { left: 880px; top: 310px; }
  .card-front .person { position: absolute; left: 130px; top: 18px; }
  .person-name { font-size: 10px; font-weight: 700; color: var(--ink); }
  .person-role { font-size: 7px; color: var(--ink-soft); margin-bottom: 8px; }
  .card-front .contact { font-size: 6.5px; line-height: 1.7; color: var(--ink-soft); }
  .card-front .contact-dot { width: 4px; height: 4px; }
  .card-front .band { height: 16px; }
</style>
</head>
<body>

  <section class="sheet letterhead" aria-label="Letterhead">
    <div class="brand"><span class="brand-square"></span><span class="brand-name">Colm Tierney Electrical</span></div>
    <div class="contact">
      <div class="contact-line"><span class="contact-dot"></span>Tel: 041 555 0192</div>
      <div class="contact-line"><span class="contact-dot"></span>Fax: 041 555 0193</div>
      <div class="contact-line"><span class="contact-dot"></span>declan@colmtierney-example.com</div>
      <div class="contact-line"><span class="contact-dot"></span>www.colmtierney-example.com</div>
    </div>
    <div class="band">
      <svg viewBox="0 0 500 22" preserveAspectRatio="none" aria-hidden="true">
        <rect x="0" y="0" width="500" height="22" fill="var(--grey-band)"/>
        <polygon points="0,0 125,0 110,22 0,22" fill="var(--grey-dark)"/>
        <polygon points="0,0 105,0 90,22 0,22" fill="var(--red)"/>
      </svg>
      <span class="band-web">www.colmtierney-example.com</span>
    </div>
  </section>

  <section class="sheet slip" aria-label="Compliments slip">
    <div class="brand"><span class="brand-square"></span><span class="brand-name">Colm Tierney Electrical</span></div>
    <p class="slip-greeting">With Best Compliment!</p>
    <div class="band">
      <svg viewBox="0 0 585 22" preserveAspectRatio="none" aria-hidden="true">
        <rect x="0" y="0" width="585" height="22" fill="var(--grey-band)"/>
        <polygon points="0,0 125,0 110,22 0,22" fill="var(--grey-dark)"/>
        <polygon points="0,0 105,0 90,22 0,22" fill="var(--red)"/>
      </svg>
      <span class="band-web">www.colmtierney-example.com</span>
    </div>
  </section>

  <section class="sheet card card-back" aria-label="Business card back">
    <div class="brand"><span class="brand-square"></span><span class="brand-name">Colm Tierney Electrical</span></div>
  </section>

  <section class="sheet card card-front" aria-label="Business card front">
    <div class="person">
      <div class="person-name">Declan Morrow</div>
      <div class="person-role">Managing Director</div>
      <div class="contact">
        <div class="contact-line"><span class="contact-dot"></span>Tel: 041 555 0192</div>
        <div class="contact-line"><span class="contact-dot"></span>Mob: 087 555 0146</div>
        <div class="contact-line"><span class="contact-dot"></span>declan@colmtierney-example.com</div>
        <div class="contact-line"><span class="contact-dot"></span>Clonbeg, Mellick Road</div>
        <div class="contact-line"><span class="contact-dot"></span>Dundalk, Louth</div>
      </div>
    </div>
    <div class="band">
      <svg viewBox="0 0 280 16" preserveAspectRatio="none" aria-hidden="true">
        <rect x="0" y="0" width="280" height="16" fill="var(--grey-band)"/>
        <polygon points="0,0 80,0 70,16 0,16" fill="var(--grey-dark)"/>
        <polygon points="0,0 66,0 56,16 0,16" fill="var(--red)"/>
      </svg>
    </div>
  </section>

</body>
</html>
```